Professional Website for Leading Global Private Equity Real Estate Company

The company is a leading global Private Equity Real Estate (PERE). We need a homepage design, an inner page design, and color/font tweaks to the logo (color should be more soothing than current blue used in the logo). The logo website should project the company as global, professional, experienced, trustworthy, accessible, YOUNG, DYNAMIC, hi-tech. PLEASE SEE the attached Design Brief Word Doc for details.

Target Market(s)

institional investors and wealthy private individuals

Industry/Entity Type

Finance

Number of Pages Required

2 page

Font styles to use
Sans Serif
Other font styles liked:
• either like in https://www.ferndalequay.com/ or like in presentations (Montserrat Black & Montserrat Light, Century Gothic, Blair ITC, Almoni Neue DL 4.0 AAA Medium, Almoni DL AAA)

Requirements
Must have
• new color palette that is NOT based on current logo. they want a more soothing color palette than the blue in that logo. the new color palette should project: global, professional, experienced, trustworthy, accessible, YOUNG, DYNAMIC, hi-tech.
Nice to have
• the likes these sites: https://www.ferndalequay.com/ and https://www.tvr.law/

```html
<!DOCTYPE html>
<html lang="en">
<head>
<meta charset="utf-8">
<title>Veyra Real Estate</title>
<link href="https://fonts.googleapis.com/css2?family=Montserrat:wght@400;500;600&family=Playfair+Display:wght@700;800&display=swap" rel="stylesheet">
<style>
:root{
  --gold-1:#a87a26;
  --gold-2:#e4c47a;
  --gold-grad:linear-gradient(90deg,#a87a26,#d7b466 60%,#e8cf8c);
  --ink:#1d1d1f;
  --text:#333;
  --muted:#666;
  --cream:#f7f1e1;
  --cream-2:#fbf8ef;
  --line:#e4dcc8;
}
*{margin:0;padding:0;box-sizing:border-box}
html,body{width:1200px;height:3386px;overflow:hidden;background:#fff}
body{font-family:"Montserrat",sans-serif;color:var(--text)}
.page{position:absolute;left:55px;top:35px;width:1092px;height:3303px;box-shadow:0 6px 30px rgba(0,0,0,.18);overflow:hidden;background:#fff}
section,header,footer{position:relative;width:1092px}
.abs{position:absolute}
.serif{font-family:"Playfair Display",serif;font-weight:800;color:var(--ink)}
.btn{position:absolute;background:var(--gold-grad);color:#2a1e08;font-size:11px;font-weight:500;display:flex;align-items:center;justify-content:center;border-radius:2px}
.dot{position:absolute;width:30px;height:30px;border-radius:50%;background:linear-gradient(135deg,#e8cf8c,#a87a26)}
.photo{position:absolute}
.hero{height:511px;background:linear-gradient(180deg,#3a3a40 0%,#2a2a2e 40%,#1c1b1d 100%)}
.hero .photo{inset:0;background:radial-gradient(ellipse at 20% 70%,rgba(150,110,60,.35),transparent 55%),linear-gradient(180deg,rgba(60,60,66,.2),rgba(20,18,18,.6))}
.brand{position:absolute;left:67px;top:14px;display:flex;align-items:center;gap:8px;color:var(--gold-2);font-weight:600;font-size:16px;letter-spacing:2px}
.brand i{width:26px;height:26px;border-radius:50%;background:var(--gold-grad)}
.nav{position:absolute;top:22px;font-size:10px;color:#eee}
.login{left:944px;top:15px;width:78px;height:28px;gap:6px}
.hero h1{position:absolute;left:0;right:0;top:150px;text-align:center;color:#fff;font-family:"Playfair Display",serif;font-size:46px;line-height:56px;font-weight:800}
.scroll{position:absolute;left:0;right:0;top:453px;text-align:center;color:#ddd;font-size:12px;letter-spacing:1px}
.about{height:387px;background:linear-gradient(180deg,var(--cream),#fbf8ef 60%,var(--cream))}
.center{position:absolute;left:0;right:0;text-align:center}
.stat{position:absolute;top:242px;width:174px;height:81px;border:1px solid var(--line);display:flex;align-items:center;gap:14px;padding-left:24px}
.stat.active{background:#fff;box-shadow:0 6px 18px rgba(0,0,0,.1);border-color:#fff}
.stat svg{width:42px;height:42px}
.stat b{display:block;font-family:"Playfair Display",serif;font-size:20px;color:var(--ink);line-height:22px}
.stat span{font-size:14px;color:var(--ink)}
.invest{height:548px;background:#fff}
.card{position:absolute;width:233px;height:194px;overflow:hidden;color:#fff}
.card .shade{position:absolute;inset:0;background:linear-gradient(180deg,rgba(0,0,0,0) 40%,rgba(0,0,0,.85))}
.card h3{position:absolute;left:18px;bottom:40px;font-size:11px;font-weight:500}
.card p{position:absolute;left:18px;bottom:14px;width:150px;font-size:7px;line-height:9px;color:#ddd}
.card .link{position:absolute;right:16px;bottom:14px;width:24px;height:24px;border-radius:50%;background:var(--gold-grad)}
.edge{height:384px;background:linear-gradient(90deg,var(--cream),#fbf8ef 50%,var(--cream))}
.panel{position:absolute;left:533px;top:56px;width:376px;height:272px;background:#fff;box-shadow:0 8px 26px rgba(0,0,0,.1)}
.copy{font-size:11px;line-height:14px;color:var(--text)}
.resp{height:415px;background:#fff}
.stay{height:288px;background:linear-gradient(180deg,var(--cream),#fcfaf3 60%,#fdfbf6)}
.field{position:absolute;border:1px solid #999;background:#fff;font-size:9px;color:#444;padding:0 12px;display:flex;align-items:center}
.touch{height:414px;background:linear-gradient(90deg,#d6d6d6,#e6e6e6 60%,#dcdcdc)}
.form{position:absolute;left:181px;top:45px;width:385px;height:369px;background:#fff}
.foot{height:356px;background:linear-gradient(180deg,#e8cf98,#f0dfb5 50%,#e9d3a0);color:#2a2a2a}
.foot .col{position:absolute;font-size:10px}
.foot h4{font-family:"Playfair Display",serif;font-size:12px;color:var(--ink);margin-bottom:10px}
.foot li{list-style:none;line-height:20.5px;font-size:10.5px}
.vline{position:absolute;top:108px;width:1px;height:171px;background:rgba(120,90,40,.3)}
</style>
</head>
<body>
<div class="page">

<header class="hero">
  <div class="photo" role="img" aria-label="Dusk skyline of tall city skyscrapers"></div>
  <div class="brand"><i></i>VEYRA</div>
  <span class="nav" style="left:509px">Home</span>
  <span class="nav" style="left:568px">About Us</span>
  <span class="nav" style="left:640px">Our Bussiness</span>
  <span class="nav" style="left:732px">Investors Lobby</span>
  <span class="nav" style="left:836px">Contact us</span>
  <svg class="abs" style="left:920px;top:22px" width="12" height="12" viewBox="0 0 12 12"><circle cx="5" cy="5" r="3.6" fill="none" stroke="#d7b466" stroke-width="1.4"/><line x1="7.6" y1="7.6" x2="11" y2="11" stroke="#d7b466" stroke-width="1.4"/></svg>
  <div class="btn login"><svg width="14" height="11" viewBox="0 0 14 11"><circle cx="5" cy="3" r="2.6" fill="#2a1e08"/><path d="M0 11c0-3 2-4.6 5-4.6S10 8 10 11z" fill="#2a1e08"/><path d="M11 3v4M9 5h4" stroke="#2a1e08" stroke-width="1.3"/></svg>Login</div>
  <h1>Leading Global Private<br>Equity Real Estate</h1>
  <div class="btn" style="left:490px;top:292px;width:111px;height:29px">About Company</div>
  <div class="scroll">SCROLL<br><svg width="16" height="10" viewBox="0 0 16 10"><path d="M2 2l6 6 6-6" fill="none" stroke="#d7b466" stroke-width="1.8"/></svg></div>
</header>

<section class="about">
  <div class="dot" style="left:531px;top:68px"></div>
  <h2 class="center serif" style="top:108px;font-size:22px">About Us &amp; Our Work</h2>
  <p class="center copy" style="left:250px;right:250px;top:161px;line-height:17px">Contrary to popular belief, Lorem Ipsum is not simply random text. It has roots in a piece of classical Latin literature from 45 BC, making it over 2000 years old. Daniel Harrow, a Latin professor at Bellmont College in Ohio, looked up one of the more obscure Latin words, consectetur.</p>
  <div class="stat" style="left:181px"><svg viewBox="0 0 42 42"><circle cx="21" cy="21" r="20" fill="none" stroke="#c9a45a" stroke-dasharray="3 3"/><circle cx="20" cy="16" r="5" fill="none" stroke="#b78c36" stroke-width="1.5"/><path d="M11 31c1-6 5-8 9-8s8 2 9 8" fill="none" stroke="#b78c36" stroke-width="1.5"/></svg><div><b>16</b><span>specialist</span></div></div>
  <div class="stat active" style="left:365px"><svg viewBox="0 0 42 42"><circle cx="21" cy="21" r="20" fill="none" stroke="#c9a45a" stroke-dasharray="3 3"/><circle cx="21" cy="15" r="3.5" fill="none" stroke="#b78c36" stroke-width="1.5"/><circle cx="13.5" cy="18" r="2.8" fill="none" stroke="#b78c36" stroke-width="1.5"/><circle cx="28.5" cy="18" r="2.8" fill="none" stroke="#b78c36" stroke-width="1.5"/><path d="M15 30c0-4 2.5-6.5 6-6.5s6 2.5 6 6.5z" fill="none" stroke="#b78c36" stroke-width="1.5"/><path d="M9 28c0-3 2-5 4.5-5M33 28c0-3-2-5-4.5-5" fill="none" stroke="#b78c36" stroke-width="1.5"/></svg><div><b>420</b><span>Client</span></div></div>
  <div class="stat" style="left:550px"><svg viewBox="0 0 42 42"><circle cx="21" cy="21" r="20" fill="none" stroke="#c9a45a" stroke-dasharray="3 3"/><rect x="12" y="12" width="18" height="18" fill="none" stroke="#b78c36" stroke-width="1.5"/><path d="M15 26v-4M20 26v-7M25 26v-10" stroke="#b78c36" stroke-width="1.5"/></svg><div><b>39</b><span>Project</span></div></div>
  <div class="stat" style="left:735px"><svg viewBox="0 0 42 42"><circle cx="21" cy="21" r="20" fill="none" stroke="#c9a45a" stroke-dasharray="3 3"/><path d="M14 12h14v5a7 7 0 0 1-14 0z" fill="none" stroke="#b78c36" stroke-width="1.5"/><path d="M21 24v4M16 30h10" stroke="#b78c36" stroke-width="1.5"/></svg><div><b>50+</b><span>Awward</span></div></div>
</section>

<section class="invest">
  <div class="dot" style="left:181px;top:80px"></div>
  <h2 class="abs serif" style="left:181px;top:122px;font-size:21px">Our Investment Plan</h2>
  <p class="abs copy" style="left:181px;top:167px;width:230px;font-size:10.5px;line-height:13px">Lorem ipsum dolor sit amet, consectetur adipiscing elit, sed do eiusmod tempor incididunt ut labore et</p>
  <div class="btn" style="left:181px;top:226px;width:110px;height:28px">Read More</div>

  <div class="card" style="left:428px;top:67px"><div class="photo" style="inset:0;background:linear-gradient(160deg,#5a7fb6,#8a8c90 55%,#3b3b3b)" role="img" aria-label="Modern apartment building under a blue sky"></div><div class="shade"></div><h3>Rental Properties</h3><p>Lorem ipsum dolor sit amet, tetur adipiscing elit, sed do eiusmod</p><div class="link"></div></div>
  <div class="card" style="left:675px;top:67px"><div class="photo" style="inset:0;background:linear-gradient(160deg,#6a6a6e,#3a3a40 60%,#222)" role="img" aria-label="Business team gathered around a table"></div><div class="shade"></div><h3>Real Estate Investment Groups</h3><p>Lorem ipsum dolor sit amet, tetur adipiscing elit, sed do eiusmod</p><div class="link"></div></div>
  <div class="card" style="left:181px;top:282px"><div class="photo" style="inset:0;background:linear-gradient(160deg,#c8ccd2,#7e7f85 55%,#3b3430)" role="img" aria-label="Hand signing papers beside a small house model"></div><div class="shade"></div><h3>House Flipping</h3><p>Lorem ipsum dolor sit amet, tetur adipiscing elit, sed do eiusmod</p><div class="link"></div></div>
  <div class="card" style="left:428px;top:282px"><div class="photo" style="inset:0;background:linear-gradient(160deg,#2e5f82,#6b3a2a 60%,#a23a2a)" role="img" aria-label="Magnifying glass over small wooden house models"></div><div class="shade"></div><h3>Real Estate Investment Trusts</h3><p>Lorem ipsum dolor sit amet, tetur adipiscing elit, sed do eiusmod</p><div class="link"></div></div>
  <div class="card" style="left:675px;top:282px"><div class="photo" style="inset:0;background:linear-gradient(160deg,#9a9ca0,#d8d8d6 50%,#3a3a3c)" role="img" aria-label="Laptop showing a property interior on screen"></div><div class="shade"></div><h3>Online Real Estate Platforms</h3><p>Lorem ipsum dolor sit amet, tetur adipiscing elit, sed do eiusmod</p><div class="link"></div></div>
</section>

<section class="edge">
  <div class="photo" style="left:181px;top:32px;width:409px;height:318px;background:linear-gradient(120deg,#2e3138,#6d727c 50%,#d7d9dd)" role="img" aria-label="Hand pointing a pen at an architectural building model"></div>
  <div class="panel">
    <div class="dot" style="left:41px;top:45px"></div>
    <h2 class="abs serif" style="left:41px;top:78px;font-size:21px">Our Edge</h2>
    <p class="abs copy" style="left:41px;top:124px;width:300px">Lorem ipsum dolor sit amet, consectetur adipiscing an elit, sed do eiusmod tempor incididunt ut labore et dolore magna aliqua. Quis ipsum suspendisse ultrices gravida. Risus commodo viverra maecenas cumsan lacus vel facilisis.</p>
    <div class="btn" style="left:43px;top:214px;width:140px;height:27px">Investor Information</div>
  </div>
</section>

<section class="resp">
  <div class="dot" style="left:181px;top:98px"></div>
  <h2 class="abs serif" style="left:181px;top:140px;font-size:21px">Our Responsibility</h2>
  <p class="abs copy" style="left:181px;top:194px;width:300px;font-size:10.5px;line-height:13.5px">There are many variations of passages of Lorem Ipsum available, but the majority have suffered alteration in some form, by injected humour, or randomised words which don't look even slightly believable. If you are going to use a passage of Lorem Ipsum, you need to be sure there isn't anything embarrassing</p>
  <div class="btn" style="left:181px;top:296px;width:110px;height:27px">Read More</div>
  <div class="photo" style="left:557px;top:72px;width:350px;height:280px;background:linear-gradient(135deg,#a9d3d3,#d8e6e6 45%,#6f7a8a)" role="img" aria-label="Group of smiling colleagues giving thumbs up"></div>
</section>

<section class="stay">
  <div class="dot" style="left:531px;top:43px"></div>
  <h2 class="center serif" style="top:84px;font-size:22px">Stay Update</h2>
  <p class="center copy" style="top:135px">Subscribe our newsletter to recive the latest news<br>and exclusive offers every week.</p>
  <div class="field" style="left:304px;top:182px;width:176px;height:33px">Phone Number</div>
  <div class="field" style="left:487px;top:182px;width:174px;height:33px">Email ID</div>
  <div class="btn" style="left:668px;top:182px;width:118px;height:33px">Subscribe Now</div>
</section>

<section class="touch">
  <div class="photo" style="left:600px;top:0;width:354px;height:414px;background:linear-gradient(180deg,#e2e2e2,#c9ccd3 55%,#7a90ad)" role="img" aria-label="Smiling woman sitting with a laptop giving thumbs up"></div>
  <div class="form">
    <h2 class="center serif" style="top:30px;font-size:21px">Get In Touch</h2>
    <div class="field" style="left:38px;top:85px;width:310px;height:30px">First Name</div>
    <div class="field" style="left:38px;top:129px;width:310px;height:30px">Last Name</div>
    <div class="field" style="left:38px;top:175px;width:310px;height:30px">Email Id</div>
    <div class="field" style="left:38px;top:221px;width:310px;height:76px;align-items:flex-start;padding-top:10px">Message...</div>
    <div class="btn" style="left:38px;top:306px;width:310px;height:29px;font-size:12px;font-weight:600">Submit now</div>
  </div>
</section>

<footer class="foot">
  <p class="abs serif" style="left:181px;top:60px;font-size:15px;line-height:20px">Much better than about our services<br>to read is to experience them....</p>
  <div class="btn" style="left:596px;top:59px;width:152px;height:30px;justify-content:space-between;padding:0 12px;font-weight:600">+43700011223<span>&raquo;</span></div>
  <div class="field" style="left:753px;top:59px;width:153px;height:30px;border:none;justify-content:space-between;font-size:11px">To contact<b style="font-size:14px">&raquo;</b></div>

  <div class="brand" style="left:181px;top:116px;font-size:15px;color:#8a6320"><i></i>VEYRA</div>
  <div class="col" style="left:181px;top:171px;line-height:15px">
    <div style="display:flex;gap:12px;margin-bottom:9px"><svg width="12" height="10" viewBox="0 0 12 10"><rect x=".5" y=".5" width="11" height="9" fill="none" stroke="#222"/><path d="M.5 .5l5.5 5 5.5-5" fill="none" stroke="#222"/></svg>office@veyra-estate.com</div>
    <div style="display:flex;gap:12px;margin-bottom:6px"><svg width="12" height="12" viewBox="0 0 12 12"><path d="M2 1l3 3-1.5 1.5a7 7 0 0 0 3 3L8 7l3 3-2 2C4 11 1 8 0 3z" fill="#222"/></svg>+43 7000 11223</div>
    <div style="display:flex;gap:12px"><svg width="12" height="14" viewBox="0 0 12 14"><path d="M6 14S1 8 1 5a5 5 0 0 1 10 0c0 3-5 9-5 9z" fill="#222"/><circle cx="6" cy="5" r="1.8" fill="#efdcae"/></svg><span>Veyra Real Estate GmbH<br>5120 Lindau, Marktweg 12</span></div>
  </div>
  <div class="vline" style="left:401px"></div>
  <div class="vline" style="left:600px"></div>
  <div class="col" style="left:478px;top:116px"><h4>Links</h4><ul><li>Home</li><li>About Us</li><li>Team</li><li>News</li><li>Extra Costs</li><li>Contact Us</li></ul></div>
  <div class="col" style="left:643px;top:116px;width:270px"><h4>Search Request</h4><p style="line-height:20.5px">Register here as a priority customer<br>and get our latest updates<br>real estate offers.</p><h4 style="margin-top:10px">Sign up for updates</h4></div>
  <div class="field" style="left:643px;top:237px;width:166px;height:29px;border:none">Enter email ID</div>
  <div class="btn" style="left:815px;top:237px;width:91px;height:29px;font-size:10px">Subscribe to</div>
  <div class="abs" style="left:181px;top:291px;width:728px;height:1px;background:rgba(120,90,40,.3)"></div>
  <p class="center" style="top:305px;font-size:10px">&copy; copy right veyra real estate 2022</p>
</footer>

</div>
</body>
</html>
```